Insurance Agency website design for Brellow Cover Insurance, LP

Build a website for Brellow Cover Insurance, LP which sells Homeowners, Auto, Renters, Condo, Flood, Disability, Life, Umbrella, and health insurance. We need the coolest insurance agency website out there to get quotes, contact us, or get additional information. Please list the following insurance companies we work with: Varnix, Ostle, Meridale Mutual, Quillor, Dunmarrow, KGZ, and Pellwick.

Make a design similar to https://www.fernagentry.com/

Selling personal insurance policies

```html
<!DOCTYPE html>
<html lang="en">
<head>
<meta charset="utf-8">
<title>Brellow Cover Insurance, LP</title>
<link href="https://fonts.googleapis.com/css2?family=Montserrat:wght@400;500;600;700&display=swap" rel="stylesheet">
<style>
:root{
  --navy:#0e4a96;
  --navy-dark:#0b3f84;
  --green:#8bc34a;
  --ink:#1d1d1f;
  --muted:#6b6f78;
  --soft:#f4f5f8;
  --line:#d9dce3;
  --white:#ffffff;
  --quote:#c9d6ea;
}
*{box-sizing:border-box;margin:0;padding:0}
html,body{width:1200px;height:4535px;overflow:hidden}
body{font-family:'Montserrat',sans-serif;color:var(--ink);background:var(--white);position:relative}
.abs{position:absolute}
.center{text-align:center;left:0;right:0}
.eyebrow{font-size:11px;font-weight:600;letter-spacing:1px;color:var(--green);text-transform:uppercase}
.heading{font-size:29px;font-weight:700;color:var(--navy)}
.rule{width:62px;height:3px;background:var(--green)}
.btn{display:flex;align-items:center;justify-content:center;font-weight:600;font-size:14px;border-radius:3px}
.btn-green{background:var(--green);color:var(--white)}

/* top bar */
.topbar{top:0;left:0;width:1200px;height:25px;background:var(--green);display:flex;justify-content:center;align-items:center;gap:28px;font-size:11px;color:var(--white);font-weight:500}
.topbar span{display:flex;align-items:center;gap:7px}
.topbar .sep{width:1px;height:16px;background:rgba(255,255,255,.6)}

/* nav */
.nav{top:25px;left:0;width:1200px;height:81px;background:var(--white)}
.brand{display:flex;align-items:center;gap:8px}
.brand-mark{width:22px;height:22px;background:var(--green)}
.brand-name{font-size:12px;font-weight:700;color:var(--navy);line-height:1.15;text-transform:uppercase}
.nav .brand{left:106px;top:22px}
.menu{font-size:13px;font-weight:500;color:#222;top:33px}
.nav .quote{left:961px;top:23px;width:134px;height:38px;background:var(--navy);color:var(--white)}

/* hero */
.hero{top:106px;left:0;width:1200px;height:626px;background:linear-gradient(180deg,#3a6db5 0%,#2b5ea8 55%,#244f93 100%)}
.hero h1{top:135px;font-size:45px;font-weight:700;color:var(--white);line-height:67px}
.hero p{top:285px;font-size:14px;color:var(--white);line-height:23px;width:720px;margin:0 auto}
.hero .btn{left:498px;top:374px;width:204px;height:43px}

/* insurances */
.card{width:246px;height:226px;text-align:center}
.card.active{background:var(--white);box-shadow:0 4px 18px rgba(0,0,0,.12);border-radius:4px}
.icon-box{width:54px;height:54px;margin:22px auto 0;border:2px solid #cfd8e6;border-radius:6px;display:flex;align-items:center;justify-content:center}
.card h3{font-size:17px;font-weight:600;margin-top:16px;color:var(--ink)}
.card.active h3{color:var(--green)}
.card p{font-size:11.5px;color:var(--muted);line-height:19px;margin:10px auto 0;width:210px}

/* about */
.about{top:1580px;left:0;width:1200px;height:597px;background:var(--soft)}
.photo{background:linear-gradient(135deg,#7c8590,#4b5462)}
.about p{font-size:11.5px;color:var(--muted);line-height:21px;width:430px}

/* partners */
.partners{top:2177px;left:0;width:1200px;height:315px;background:linear-gradient(180deg,#2b5aa0,#1f4c93);overflow:hidden}
.partner{top:188px;width:186px;height:57px;background:var(--white);display:flex;align-items:center;justify-content:center;font-size:17px;font-weight:600;color:var(--navy)}

/* testimonials */
.tcard{width:446px;height:228px;background:var(--white);box-shadow:0 4px 20px rgba(0,0,0,.08);border-radius:6px;text-align:center}
.tcard .qm{position:absolute;left:20px;top:-10px;font-size:86px;font-weight:700;color:var(--quote);line-height:1}
.tcard p{font-size:11px;color:#555;line-height:23px;width:402px;margin:40px auto 0}
.person{display:flex;align-items:center;justify-content:center;gap:12px;margin-top:18px}
.avatar{width:54px;height:54px;border-radius:50%;background:linear-gradient(135deg,#b4a08c,#6b5a4c)}
.person .nm{font-size:15px;font-weight:600;color:var(--navy);text-align:left}
.stars{color:#f2a81d;font-size:16px;letter-spacing:2px}
.arrow{width:32px;height:32px;border-radius:50%;display:flex;align-items:center;justify-content:center}
.dot{width:7px;height:7px;border-radius:50%;background:#c8ccd4;top:2991px}

/* contact */
.contact{top:3094px;left:0;width:1200px;height:611px;background:var(--soft)}
.field{background:var(--white);border:1px solid var(--line);border-radius:3px;font-size:11px;color:#8a8e96;padding:14px 14px}

/* cta & footer */
.footer{top:3942px;left:0;width:1200px;height:593px;background:var(--navy)}
.cta{top:3801px;left:141px;width:917px;height:284px;background:var(--green);border-radius:14px;text-align:center;color:var(--white)}
.cta h2{font-size:28px;font-weight:700;margin-top:70px}
.cta p{font-size:12px;font-weight:500;line-height:21px;width:700px;margin:13px auto 0}
.cta .btn{position:absolute;left:352px;top:191px;width:215px;height:44px;background:var(--white);color:var(--navy)}
.footer .brand-name{color:var(--white)}
.social{width:35px;height:35px;border-radius:50%;background:var(--white)}
.fcol{width:300px;text-align:center;color:var(--white)}
.fcol h4{font-size:14px;font-weight:600;margin-top:12px}
.fcol p{font-size:12px;line-height:22px;margin-top:8px;color:#dbe4f2}
.vline{width:1px;height:115px;background:rgba(255,255,255,.25)}
.hline{left:141px;width:917px;height:1px;background:rgba(255,255,255,.25)}
.legal{font-size:12px;color:var(--white)}
</style>
</head>
<body>

<!-- top bar -->
<div class="abs topbar">
  <span><svg width="11" height="11" viewBox="0 0 24 24"><path fill="#fff" d="M6.6 10.8a15 15 0 0 0 6.6 6.6l2.2-2.2c.3-.3.7-.4 1-.2 1.1.4 2.3.6 3.6.6.6 0 1 .4 1 1V20c0 .6-.4 1-1 1A17 17 0 0 1 3 4c0-.6.4-1 1-1h3.5c.6 0 1 .4 1 1 0 1.3.2 2.5.6 3.6.1.3 0 .7-.2 1z"/></svg>Phone: 555-014-2290</span>
  <span class="sep"></span>
  <span><svg width="12" height="10" viewBox="0 0 24 18"><path fill="#fff" d="M0 0h24v18H0z"/><path d="M1 1l11 8 11-8" stroke="#8bc34a" stroke-width="2" fill="none"/></svg>E-Mail: info@brellowcover.com</span>
</div>

<!-- nav -->
<header class="abs nav">
  <div class="abs brand"><span class="brand-mark"></span><span class="brand-name">Brellow Cover<br>Insurance</span></div>
  <span class="abs menu" style="left:310px">HOME</span>
  <span class="abs menu" style="left:390px">ABOUT US</span>
  <span class="abs menu" style="left:499px">INSURANCE <svg width="10" height="7" viewBox="0 0 10 7"><path d="M1 1l4 4 4-4" stroke="#222" stroke-width="1.5" fill="none"/></svg></span>
  <span class="abs menu" style="left:635px">MARKET PARTNERS</span>
  <span class="abs menu" style="left:804px">CONTACT</span>
  <div class="abs btn quote">Get a Quote</div>
</header>

<!-- hero -->
<section class="abs hero" role="img" aria-label="Family at home holding a white roof shape over their heads, with a blue overlay">
  <h1 class="abs center" style="text-align:center">Protect What Matters Most with<br>Trusted Insurance</h1>
  <p class="abs center" style="text-align:center">At Brellow Cover Insurance, we understand how crucial it is to protect the things that matter most to you - your home, health, and family.</p>
  <div class="abs btn btn-green">Get Your Quote Now</div>
</section>

<!-- insurances -->
<div class="abs center eyebrow" style="top:823px;text-align:center">Our Insurances</div>
<h2 class="abs center heading" style="top:850px;text-align:center">Our Various Insurance Solutions</h2>
<div class="abs rule" style="top:894px;left:569px"></div>

<div class="abs card active" style="left:106px;top:941px">
  <div class="icon-box"><svg width="30" height="30" viewBox="0 0 30 30"><path d="M4 14L15 4l11 10v12H4z" fill="none" stroke="#0e4a96" stroke-width="2.2"/><circle cx="15" cy="17" r="4" fill="none" stroke="#0e4a96" stroke-width="2"/><path d="M18 20l3 3" stroke="#0e4a96" stroke-width="2"/></svg></div>
  <h3>Homeowners</h3>
  <p>Protect your home and belongings from damage, theft, or disaster with comprehensive homeowners coverage.</p>
</div>
<div class="abs card" style="left:375px;top:941px">
  <div class="icon-box"><svg width="30" height="30" viewBox="0 0 30 30"><path d="M5 15l3-7h14l3 7v7H5z" fill="#0e4a96"/><rect x="9" y="10" width="12" height="4" fill="#fff"/><circle cx="9" cy="18" r="1.8" fill="#fff"/><circle cx="21" cy="18" r="1.8" fill="#fff"/></svg></div>
  <h3>Auto Insurance</h3>
  <p>Safeguard your vehicle against accidents, theft, or damage, ensuring you're covered on the road.</p>
</div>
<div class="abs card" style="left:621px;top:941px">
  <div class="icon-box"><svg width="30" height="30" viewBox="0 0 30 30"><path d="M4 12L15 5l11 7" fill="none" stroke="#0e4a96" stroke-width="2.2"/><rect x="7" y="13" width="16" height="12" fill="none" stroke="#0e4a96" stroke-width="2"/><rect x="12" y="17" width="6" height="8" fill="#0e4a96"/></svg></div>
  <h3>Renters Insurance</h3>
  <p>Protect personal belongings in a rental space, covering damage, theft, or loss due to disasters.</p>
</div>
<div class="abs card" style="left:868px;top:941px">
  <div class="icon-box"><svg width="30" height="30" viewBox="0 0 30 30"><rect x="8" y="4" width="14" height="22" fill="#0e4a96"/><g fill="#fff"><rect x="11" y="7" width="3" height="3"/><rect x="16" y="7" width="3" height="3"/><rect x="11" y="12" width="3" height="3"/><rect x="16" y="12" width="3" height="3"/><rect x="11" y="17" width="3" height="3"/><rect x="16" y="17" width="3" height="3"/></g></svg></div>
  <h3>Condo Insurance</h3>
  <p>Cover your condo unit and personal property, filling the gap not covered by the building's insurance.</p>
</div>

<div class="abs card" style="left:106px;top:1190px">
  <div class="icon-box"><svg width="30" height="30" viewBox="0 0 30 30"><path d="M6 14l9-8 9 8v6H6z" fill="#0e4a96"/><path d="M3 22c3-2 5 2 8 0s5 2 8 0 5 2 8 0M3 26c3-2 5 2 8 0s5 2 8 0 5 2 8 0" stroke="#0e4a96" stroke-width="1.8" fill="none"/></svg></div>
  <h3>Flood Insurance</h3>
  <p>Provide financial protection against water damage caused by floods, which are often excluded from standard coverage.</p>
</div>
<div class="abs card" style="left:375px;top:1190px">
  <div class="icon-box"><svg width="30" height="30" viewBox="0 0 30 30"><circle cx="14" cy="5" r="2.5" fill="#0e4a96"/><path d="M14 9v8h7l3 7" stroke="#0e4a96" stroke-width="2.4" fill="none"/><path d="M11 13a7 7 0 1 0 7 10" stroke="#0e4a96" stroke-width="2.2" fill="none"/></svg></div>
  <h3>Disability Insurance</h3>
  <p>Receive income replacement if you're unable to work due to illness or injury, ensuring financial security.</p>
</div>
<div class="abs card" style="left:621px;top:1190px">
  <div class="icon-box"><svg width="30" height="30" viewBox="0 0 30 30"><path d="M15 26S3 18 3 10a6 6 0 0 1 12-1 6 6 0 0 1 12 1c0 8-12 16-12 16z" fill="#0e4a96"/><path d="M15 10v8M11 14h8" stroke="#fff" stroke-width="2.4"/></svg></div>
  <h3>Life Insurance</h3>
  <p>Protect your loved ones financially after your passing, covering funeral expenses and ongoing living costs.</p>
</div>
<div class="abs card" style="left:868px;top:1190px">
  <div class="icon-box"><svg width="30" height="30" viewBox="0 0 30 30"><path d="M15 3l10 4v8c0 6-5 10-10 12C10 25 5 21 5 15V7z" fill="#0e4a96"/><circle cx="15" cy="15" r="5" fill="#fff"/><path d="M15 12v6M12 15h6" stroke="#0e4a96" stroke-width="2"/></svg></div>
  <h3>Health Insurance</h3>
  <p>Cover medical expenses, from check-ups to emergencies, ensuring you get the care you need without financial strain.</p>
</div>

<div class="abs btn btn-green" style="left:533px;top:1447px;width:134px;height:40px">Explore All</div>

<!-- about -->
<section class="abs about">
  <div class="abs photo" style="left:141px;top:71px;width:294px;height:348px" role="img" aria-label="Insurance agent handing keys to a smiling couple"></div>
  <div class="abs" style="left:237px;top:306px;width:307px;height:219px;background:var(--white);border-radius:8px;padding:8px">
    <div class="photo" style="width:100%;height:100%;border-radius:6px;background:linear-gradient(135deg,#d9a47c,#b07553)" role="img" aria-label="Hands holding a small model house"></div>
  </div>
  <div class="abs eyebrow" style="left:616px;top:96px">Who We Are</div>
  <h2 class="abs heading" style="left:616px;top:122px;line-height:40px">About Brellow Cover<br>Insurance</h2>
  <div class="abs rule" style="left:616px;top:213px"></div>
  <p class="abs" style="left:616px;top:242px">At Brellow Cover Insurance, we're dedicated to providing you with reliable, comprehensive insurance solutions tailored to your needs. Our mission is simple: to offer you peace of mind with the protection you deserve. We specialize in home, auto, health, and life insurance, and our experienced team is committed to helping you find the right coverage for every stage of life.</p>
  <p class="abs" style="left:616px;top:383px">Founded with a focus on customer satisfaction, Brellow Cover Insurance has grown to become a trusted partner in securing what matters most.</p>
  <div class="abs btn btn-green" style="left:616px;top:460px;width:139px;height:42px">Learn More</div>
</section>

<!-- partners -->
<section class="abs partners" role="img" aria-label="Business people shaking hands, with a blue overlay">
  <div class="abs center eyebrow" style="top:70px;text-align:center">Our Partners</div>
  <h2 class="abs center" style="top:100px;text-align:center;font-size:28px;font-weight:700;color:var(--white)">Trusted Partners for Your Protection</h2>
  <div class="abs rule" style="top:144px;left:569px"></div>
  <div class="abs partner" style="left:-70px">Varnix</div>
  <div class="abs partner" style="left:160px">Ostle</div>
  <div class="abs partner" style="left:391px">Meridale Mutual</div>
  <div class="abs partner" style="left:623px">Quillor</div>
  <div class="abs partner" style="left:854px">Dunmarrow</div>
  <div class="abs partner" style="left:1084px">Pellwick</div>
</section>

<!-- testimonials -->
<div class="abs center eyebrow" style="top:2584px;text-align:center">Clients Testimonials</div>
<h2 class="abs center heading" style="top:2610px;text-align:center">Proven Success Stories</h2>
<div class="abs rule" style="top:2656px;left:569px"></div>

<div class="abs tcard" style="left:141px;top:2716px">
  <span class="qm">&ldquo;</span>
  <p>It is a long established fact that a reader will be distracted by the readable content of a page when looking at its layout. The point of using Lorem Ipsum is that it has a more-or-less normal distribution of letters, as opposed to using 'Content here, content here'.</p>
  <div class="person"><div class="avatar" role="img" aria-label="Client portrait"></div><div><div class="nm">Dalen Orwick</div><div class="stars">★★★★★</div></div></div>
</div>
<div class="abs tcard" style="left:612px;top:2716px">
  <span class="qm">&ldquo;</span>
  <p>It is a long established fact that a reader will be distracted by the readable content of a page when looking at its layout. The point of using Lorem Ipsum is that it has a more-or-less normal distribution of letters, as opposed to using 'Content here, content here'.</p>
  <div class="person"><div class="avatar" role="img" aria-label="Client portrait"></div><div><div class="nm">Tomas Prell</div><div class="stars">★★★★★</div></div></div>
</div>
<div class="abs arrow" style="left:125px;top:2813px;background:var(--white)"><svg width="14" height="12" viewBox="0 0 14 12"><path d="M13 6H2M6 1L1 6l5 5" stroke="#8bc34a" stroke-width="1.8" fill="none"/></svg></div>
<div class="abs arrow" style="left:1042px;top:2813px;background:var(--green)"><svg width="14" height="12" viewBox="0 0 14 12"><path d="M1 6h11M8 1l5 5-5 5" stroke="#fff" stroke-width="1.8" fill="none"/></svg></div>
<span class="abs dot" style="left:555px"></span>
<span class="abs dot" style="left:574px"></span>
<span class="abs dot" style="left:592px;top:2987px;width:15px;height:15px;background:var(--navy)"></span>
<span class="abs dot" style="left:617px"></span>
<span class="abs dot" style="left:636px"></span>

<!-- contact -->
<section class="abs contact">
  <div class="abs eyebrow" style="left:141px;top:86px">Contact Us</div>
  <h2 class="abs heading" style="left:141px;top:110px">Get in Touch with Us</h2>
  <div class="abs rule" style="left:141px;top:157px"></div>
  <div class="abs field" style="left:141px;top:202px;width:227px;height:41px">First Name</div>
  <div class="abs field" style="left:387px;top:202px;width:227px;height:41px">Last Name</div>
  <div class="abs field" style="left:141px;top:264px;width:227px;height:41px">Email</div>
  <div class="abs field" style="left:387px;top:264px;width:227px;height:41px">Phone</div>
  <div class="abs field" style="left:141px;top:326px;width:473px;height:119px">Message</div>
  <div class="abs btn btn-green" style="left:141px;top:489px;width:146px;height:41px">Submit Now</div>
  <div class="abs photo" style="left:681px;top:70px;width:379px;height:474px;border-radius:14px;background:linear-gradient(135deg,#8a99a8,#3b434e)" role="img" aria-label="Agent reviewing a policy document with a client in an office"></div>
</section>

<!-- footer & CTA -->
<footer class="abs footer">
  <div class="abs brand" style="left:141px;top:218px"><span class="brand-mark"></span><span class="brand-name">Brellow Cover<br>Insurance</span></div>
  <p class="abs" style="left:341px;top:218px;width:500px;font-size:11px;line-height:20px;color:#dbe4f2">Brellow Cover Insurance, we're dedicated to providing you with reliable, comprehensive insurance solutions tailored to your needs.</p>
  <span class="abs social" style="left:926px;top:213px" aria-label="Social profile"></span>
  <span class="abs social" style="left:974px;top:213px;background:var(--green)" aria-label="Social profile"></span>
  <span class="abs social" style="left:1023px;top:213px" aria-label="Social profile"></span>
  <div class="abs hline" style="top:280px"></div>
  <div class="abs center" style="top:318px;text-align:center;font-size:15px;font-weight:600;color:var(--white)">Contact Information</div>

  <div class="abs fcol" style="left:131px;top:364px">
    <svg width="18" height="18" viewBox="0 0 24 24"><path fill="#8bc34a" d="M6.6 10.8a15 15 0 0 0 6.6 6.6l2.2-2.2c.3-.3.7-.4 1-.2 1.1.4 2.3.6 3.6.6.6 0 1 .4 1 1V20c0 .6-.4 1-1 1A17 17 0 0 1 3 4c0-.6.4-1 1-1h3.5c.6 0 1 .4 1 1 0 1.3.2 2.5.6 3.6.1.3 0 .7-.2 1z"/></svg>
    <h4>Call Us</h4><p>(555)-014-2290</p>
  </div>
  <div class="abs fcol" style="left:436px;top:364px">
    <svg width="16" height="20" viewBox="0 0 16 20"><path d="M8 19s6-6.5 6-11A6 6 0 0 0 2 8c0 4.5 6 11 6 11z" fill="none" stroke="#8bc34a" stroke-width="2"/><circle cx="8" cy="8" r="2.3" fill="#8bc34a"/></svg>
    <h4>Find Us</h4><p>123, Lorem Ipsum is simply dummy<br>text of the printing</p>
  </div>
  <div class="abs fcol" style="left:769px;top:364px">
    <svg width="22" height="16" viewBox="0 0 24 18"><path fill="#8bc34a" d="M0 0h24v18H0z"/><path d="M1 1l11 8 11-8" stroke="#0e4a96" stroke-width="2" fill="none"/></svg>
    <h4>Email Address</h4><p>info@brellowcover.com</p>
  </div>
  <div class="abs vline" style="left:398px;top:361px"></div>
  <div class="abs vline" style="left:774px;top:361px"></div>
  <div class="abs hline" style="top:516px"></div>
  <span class="abs legal" style="left:141px;top:544px">Copyright © 2025 Brellow Cover Insurance - All Rights Reserved.</span>
  <span class="abs legal" style="left:862px;top:544px">Terms of use</span>
  <span class="abs legal" style="left:973px;top:544px">Privacy Policy</span>
</footer>

<div class="abs cta">
  <h2>Secure a Future with Customized Quote Today!</h2>
  <p>Protect what matters most with tailored insurance solutions. Get a personalized quote today and secure peace of mind.</p>
  <div class="btn">Get a Quote</div>
</div>

</body>
</html>
```